Layout for site fence advertising - length approx. 250 cm x 125 cm

The advertising will later be printed on a PVC film and used for events or on sports fields.

Main services :
Your regional contact at
Real estate and business financing
independent insurance advice

```html
<!DOCTYPE html>
<html lang="en">
<head>
<meta charset="utf-8">
<title>Fence Banner – Real Estate and Business Financing</title>
<link rel="stylesheet" href="https://fonts.googleapis.com/css2?family=Bebas+Neue&family=Poppins:wght@500;600;700;800&display=swap">
<style>
  :root {
    --brand-blue: #1f56c3;
    --brand-red: #8d1b1e;
    --ink: #1f1f22;
    --band-dark: #1d1d1f;
    --paper: #ffffff;
    --sky-top: #e9f1fb;
    --sky-bottom: #ffffff;
    --muted: #4a4a4f;
  }
  * { box-sizing: border-box; margin: 0; padding: 0; }
  html, body { width: 912px; height: 1200px; overflow: hidden; }
  body {
    background: var(--paper);
    font-family: "Poppins", sans-serif;
    position: relative;
  }
  .banner {
    position: absolute;
    left: 26px; top: 385px;
    width: 860px; height: 430px;
    background: linear-gradient(180deg, var(--sky-top) 0%, var(--sky-bottom) 40%, #f2f5fa 100%);
    box-shadow: 0 10px 40px rgba(0,0,0,0.18);
    overflow: hidden;
  }
  .headline-top {
    position: absolute; left: 21px; top: 27px;
    font-family: "Poppins", sans-serif; font-weight: 800;
    font-size: 55px; line-height: 1; letter-spacing: -0.5px;
    color: var(--brand-blue); white-space: nowrap;
  }
  .headline-main {
    position: absolute; left: 21px; top: 76px;
    font-family: "Bebas Neue", sans-serif;
    font-size: 80px; line-height: 1;
    color: var(--brand-red); white-space: nowrap;
  }
  .headline-rule {
    position: absolute; left: 25px; top: 159px;
    width: 503px; height: 3px; background: var(--brand-blue);
  }
  .subline {
    position: absolute; left: 26px; top: 174px;
    font-weight: 600; font-size: 35px; line-height: 1;
    color: var(--ink); white-space: nowrap;
  }
  .advice-lead {
    position: absolute; left: 26px; top: 220px;
    font-weight: 700; font-size: 23px; line-height: 1;
    color: var(--brand-blue); white-space: nowrap;
  }
  .service-band {
    position: absolute; left: 0; top: 277px;
    width: 720px; height: 58px; background: var(--brand-blue);
  }
  .service {
    position: absolute; top: 255px;
    display: flex; flex-direction: column; align-items: center;
    transform: translateX(-50%);
  }
  .service-icon {
    width: 38px; height: 38px; border-radius: 50%;
    background: var(--paper); border: 2px solid var(--brand-blue);
    display: flex; align-items: center; justify-content: center;
  }
  .service-label {
    margin-top: 8px; color: var(--paper);
    font-weight: 600; font-size: 20px; white-space: nowrap;
  }
  .service-divider {
    position: absolute; top: 284px; width: 1px; height: 44px;
    background: rgba(255,255,255,0.25);
  }
  .contact-band {
    position: absolute; left: 0; top: 335px;
    width: 860px; height: 95px; background: var(--band-dark);
  }
  .regional {
    position: absolute; left: 28px; top: 353px;
    font-family: "Bebas Neue", sans-serif; color: var(--paper);
    font-size: 30px; line-height: 0.95;
  }
  .regional .big { font-size: 36px; }
  .contact-divider {
    position: absolute; left: 184px; top: 348px;
    width: 2px; height: 62px; background: var(--brand-red);
  }
  .contact-line {
    position: absolute; left: 209px;
    display: flex; align-items: center; gap: 12px;
    color: var(--paper); font-weight: 600; font-size: 25px; line-height: 1;
    white-space: nowrap;
  }
  .contact-line.phone { top: 349px; }
  .contact-line.web { top: 383px; }
  .advisor-name {
    position: absolute; left: 552px; top: 355px;
    font-weight: 700; font-size: 22px; line-height: 1.1;
    white-space: nowrap; z-index: 2;
  }
  .advisor-name .first { color: var(--brand-blue); display: block; }
  .advisor-name .last { color: var(--paper); display: block; }
  .brand {
    position: absolute; left: 541px; top: 32px;
    display: flex; align-items: center;
  }
  .brand-dot {
    width: 72px; height: 72px; border-radius: 50%;
    border: 3px solid var(--brand-blue); flex: none;
  }
  .brand-rule {
    width: 2px; height: 82px; background: var(--muted); margin: 0 8px 0 10px; flex: none;
  }
  .brand-name {
    font-weight: 600; font-size: 14px; color: var(--brand-blue); line-height: 1.2;
    white-space: nowrap;
  }
  .brand-tagline {
    font-weight: 500; font-size: 11.5px; color: var(--muted); margin-top: 3px;
    white-space: nowrap;
  }
  .advisor-photo {
    position: absolute; left: 672px; top: 112px;
    width: 188px; height: 318px;
    background: linear-gradient(180deg, #c9a892 0%, #b88f78 45%, #e8e8ec 70%, #2a2a33 100%);
    border-radius: 90px 90px 0 0;
  }
</style>
</head>
<body>
  <main class="banner">
    <h1 class="headline-top">REAL ESTATE AND</h1>
    <div class="headline-main">BUSINESS FINANCING</div>
    <div class="headline-rule"></div>

    <div class="brand">
      <div class="brand-dot"></div>
      <div class="brand-rule"></div>
      <div>
        <div class="brand-name">Brenner Finanzberatung GmbH</div>
        <div class="brand-tagline">Finanzieren, Versichern, Vorsorgen</div>
      </div>
    </div>

    <h2 class="subline">INDEPENDENT INSURANCE ADVICER</h2>
    <p class="advice-lead">YOUR PERSONAL FINANCIAL ADVICE FOR:</p>

    <div class="service-band"></div>
    <div class="service-divider" style="left:183px"></div>
    <div class="service-divider" style="left:443px"></div>

    <div class="service" style="left:93px">
      <div class="service-icon">
        <svg width="20" height="20" viewBox="0 0 20 20"><circle cx="10" cy="12" r="6" fill="var(--brand-red)"/><path d="M10 6 L6 2 M10 6 L14 2" stroke="var(--brand-red)" stroke-width="2" fill="none"/><text x="10" y="15" text-anchor="middle" font-size="8" font-family="Poppins, sans-serif" font-weight="700" fill="#fff">$</text></svg>
      </div>
      <span class="service-label">Investment</span>
    </div>
    <div class="service" style="left:329px">
      <div class="service-icon">
        <svg width="22" height="22" viewBox="0 0 22 22"><ellipse cx="8" cy="6" rx="6" ry="2.5" fill="var(--brand-red)"/><ellipse cx="8" cy="10" rx="6" ry="2.5" fill="var(--brand-red)"/><ellipse cx="8" cy="14" rx="6" ry="2.5" fill="var(--brand-red)"/><circle cx="15" cy="14" r="5.5" fill="var(--brand-red)" stroke="#fff" stroke-width="1.2"/><text x="15" y="17" text-anchor="middle" font-size="8" font-family="Poppins, sans-serif" font-weight="700" fill="#fff">$</text></svg>
      </div>
      <span class="service-label">Financing &amp; Leasing</span>
    </div>
    <div class="service" style="left:564px">
      <div class="service-icon">
        <svg width="18" height="20" viewBox="0 0 18 20"><path d="M9 1 L17 4 V10 C17 15 13 18 9 19 C5 18 1 15 1 10 V4 Z" fill="var(--brand-red)"/><path d="M5.5 10 L8 12.5 L12.5 7.5" stroke="#fff" stroke-width="1.8" fill="none"/></svg>
      </div>
      <span class="service-label">Insurance</span>
    </div>

    <div class="contact-band"></div>
    <div class="regional"><span>YOUR REGIONAL</span><br><span class="big">CONTACT AT</span></div>
    <div class="contact-divider"></div>

    <div class="contact-line phone">
      <svg width="18" height="18" viewBox="0 0 18 18"><circle cx="9" cy="9" r="9" fill="var(--brand-blue)"/><path d="M6 4.5 L7.6 6.8 L6.8 8 C7.4 9.4 8.6 10.6 10 11.2 L11.2 10.4 L13.5 12 L12.6 13.6 C9 13.4 4.6 9 4.4 5.4 Z" fill="#fff"/></svg>
      <span>+43 660 124 5870</span>
    </div>
    <div class="contact-line web">
      <svg width="18" height="18" viewBox="0 0 18 18"><circle cx="9" cy="9" r="8" fill="none" stroke="var(--brand-blue)" stroke-width="2"/><ellipse cx="9" cy="9" rx="3.5" ry="8" fill="none" stroke="var(--brand-blue)" stroke-width="1.5"/><path d="M1 9 H17 M2.5 5 H15.5 M2.5 13 H15.5" stroke="var(--brand-blue)" stroke-width="1.5"/></svg>
      <span>www.brenner-finanz.at</span>
    </div>

    <div class="advisor-photo" role="img" aria-label="Portrait photo of the advisor in a dark suit and white shirt"></div>

    <div class="advisor-name"><span class="first">MARKUS</span><span class="last">BRENNER</span></div>
  </main>
</body>
</html>
```